Stylish business cards for KV7

To create an appealing and professional business card design for a WOMEN Owned Construction Supply Company.
2 sided card. Incorporate brand elements, curvy, colorful, sleek and bright. No solid white background. attached samples of styles added shapes/ribbons. Want something with that WOW that looks awesome, factor. It is a new logo, so feel free to mess with logo colors in the blue and teal factors that can look good with both dark and light background. If you want to try a watermark with just the KV7, without the "Supply" that might look cool to.

Industry/Entity Type

Women owned construction supply company

Contact Information for Business Card

Name, Title, and phone number and email, web page. maybe spot for qr code.

Font styles to use
Sans Serif

Requirements
Nice to have
• would love to see colors, maybe stylish ribbon dividers or some sort of 2 or 3 tone color card that compliments logo.
Should not have
• Please do not have all white background. Do not include Home/reale state/ or building images.

```html
<!DOCTYPE html>
<html lang="en">
<head>
<meta charset="utf-8">
<title>KV7 Supply – Business Cards</title>
<link href="https://fonts.googleapis.com/css2?family=Poppins:wght@400;500;600&display=swap" rel="stylesheet">
<style>
  :root {
    --page-bg: #2b2b2d;
    --navy: #1f3a5c;
    --navy-panel: #2a4467;
    --teal: #2a9cc4;
    --teal-light: #35a8d3;
    --white: #ffffff;
    --silver: #d9dde2;
    --text-light: #e8eef5;
    --logo-dark: #3a5577;
  }
  * { box-sizing: border-box; margin: 0; padding: 0; }
  html, body {
    width: 1200px; height: 875px; overflow: hidden;
    background: var(--page-bg);
    font-family: "Poppins", sans-serif;
  }
  .sheet {
    width: 1200px; height: 875px;
    display: flex; flex-direction: column;
    align-items: center; justify-content: center; gap: 36px;
  }
  .card {
    position: relative;
    width: 680px; height: 389px;
    border-radius: 26px;
    overflow: hidden;
    box-shadow: 0 14px 30px rgba(0,0,0,.45);
  }
  .card-front { background: var(--navy); }
  .wordmark {
    position: absolute;
    display: flex; align-items: center; gap: 14px;
    font-weight: 600; letter-spacing: .5px; white-space: nowrap;
  }
  .card-front .wordmark {
    left: 50%; top: 50%; transform: translate(-50%, -50%);
    font-size: 58px; color: var(--silver);
  }
  .wordmark .mark-dot {
    width: 22px; height: 22px; border-radius: 50%;
    background: currentColor;
  }
  .card-back { background: var(--white); }
  .card-back .shapes { position: absolute; inset: 0; width: 100%; height: 100%; }
  .card-back .wordmark {
    left: 62px; top: 50%; transform: translateY(-50%);
    font-size: 42px; color: var(--logo-dark);
  }
  .contact {
    position: absolute; left: 468px; top: 62px; width: 190px;
    color: var(--text-light);
  }
  .contact-name {
    font-size: 19px; font-weight: 600; letter-spacing: .6px;
    color: var(--teal-light); text-transform: uppercase; white-space: nowrap;
  }
  .contact-title { font-size: 13px; margin-top: 2px; }
  .contact-address { font-size: 13px; line-height: 1.45; margin-top: 18px; white-space: nowrap; }
  .contact-list { list-style: none; margin-top: 18px; font-size: 13px; line-height: 1.75; }
  .contact-list li { display: flex; align-items: center; gap: 10px; white-space: nowrap; }
  .contact-list svg { width: 12px; height: 12px; fill: var(--teal-light); flex: none; }
</style>
</head>
<body>
<main class="sheet">
  <section class="card card-front" aria-label="Business card front">
    <div class="wordmark"><span class="mark-dot"></span>KV7 Supply</div>
  </section>

  <section class="card card-back" aria-label="Business card back">
    <svg class="shapes" viewBox="0 0 680 389" preserveAspectRatio="none" aria-hidden="true">
      <polygon points="405,0 680,0 680,389 475,389 395,215 440,60" fill="var(--navy-panel)"/>
      <polygon points="300,0 405,0 440,60" fill="var(--teal)"/>
      <polygon points="395,215 475,389 560,389" fill="var(--teal)"/>
    </svg>

    <div class="wordmark"><span class="mark-dot"></span>KV7 Supply</div>

    <div class="contact">
      <p class="contact-name">Dana Whitfield</p>
      <p class="contact-title">General Manager</p>
      <p class="contact-address">48 Granite Row<br>Lakeview, OH 44101 USA</p>
      <ul class="contact-list">
        <li>
          <svg viewBox="0 0 24 24"><path d="M6.6 10.8a15.1 15.1 0 006.6 6.6l2.2-2.2a1 1 0 011-.25 11.4 11.4 0 003.6.57 1 1 0 011 1V20a1 1 0 01-1 1A17 17 0 013 4a1 1 0 011-1h3.5a1 1 0 011 1c0 1.25.2 2.45.57 3.57a1 1 0 01-.25 1z"/></svg>
          +1.555.010.246
        </li>
        <li>
          <svg viewBox="0 0 24 24"><path d="M2 5h20v14H2z"/></svg>
          name@kv7supply.com
        </li>
        <li>
          <svg viewBox="0 0 24 24"><circle cx="12" cy="12" r="10"/></svg>
          www.kv7supply.com
        </li>
      </ul>
    </div>
  </section>
</main>
</body>
</html>
```